Dunmore Roofing

Want a professional looking business card

Industry/Entity Type

Business

Contact Information for Business Card

Paul Dunmore ( Owner) paul@dunmoreroofing-example.com, www.dunmoreroofing-example.com, Adress: 4172 Township road 43 Ashcombe,ON K9X4T2

```html
<!DOCTYPE html>
<html lang="en">
<head>
<meta charset="utf-8">
<title>Dunmore Roofing – Business Card</title>
<link href="https://fonts.googleapis.com/css2?family=Open+Sans:wght@400;700;800&display=swap" rel="stylesheet">
<style>
  :root {
    --page-bg: #e7e8eb;
    --brand-blue: #1c4586;
    --stripe-grey: #7a7c80;
    --paper-white: #f1f0ef;
    --paper-shade: #e4e3e2;
    --text-light: #ffffff;
    --text-muted: #e3e9f3;
  }
  html, body {
    margin: 0;
    width: 1200px;
    height: 900px;
    overflow: hidden;
    background: var(--page-bg);
    font-family: "Open Sans", Arial, sans-serif;
  }
  .business-card {
    position: absolute;
    left: 80px;
    top: 128px;
    width: 1040px;
    height: 643px;
    overflow: hidden;
    box-shadow: 0 18px 40px rgba(0,0,0,0.18);
  }
  .card-shapes {
    position: absolute;
    inset: 0;
    width: 100%;
    height: 100%;
  }
  .contact-block {
    position: absolute;
    left: 61px;
    top: 0;
    color: var(--text-light);
  }
  .owner-name {
    position: absolute;
    top: 76px;
    margin: 0;
    font-size: 38px;
    font-weight: 700;
    letter-spacing: 0.5px;
    white-space: nowrap;
  }
  .owner-role {
    position: absolute;
    top: 124px;
    margin: 0;
    font-size: 24px;
    color: var(--text-muted);
    white-space: nowrap;
  }
  .contact-line {
    position: absolute;
    display: flex;
    align-items: center;
    gap: 10px;
    font-size: 25px;
    white-space: nowrap;
  }
  .contact-line svg { width: 22px; height: 22px; flex: none; }
  .contact-email { top: 201px; }
  .contact-web { top: 238px; }
  .address {
    position: absolute;
    top: 301px;
    margin: 0;
    font-size: 26px;
    line-height: 38px;
    font-style: normal;
    white-space: nowrap;
  }
  .brand-name {
    position: absolute;
    left: 560px;
    top: 330px;
    width: 400px;
    margin: 0;
    display: flex;
    flex-direction: column;
    align-items: center;
    color: var(--brand-blue);
    font-size: 62px;
    font-weight: 800;
    line-height: 1.05;
    letter-spacing: 4px;
    text-align: center;
  }
</style>
</head>
<body>
  <div class="business-card">
    <svg class="card-shapes" viewBox="0 0 652 403" preserveAspectRatio="none" aria-hidden="true">
      <defs>
        <linearGradient id="paperTone" x1="0" y1="0" x2="1" y2="1">
          <stop offset="0" stop-color="var(--paper-white)"/>
          <stop offset="1" stop-color="var(--paper-shade)"/>
        </linearGradient>
      </defs>
      <rect class="card-base" width="652" height="403" fill="var(--brand-blue)"/>
      <polygon class="card-panel" points="505,0 511,0 652,160 652,403 160,403" fill="url(#paperTone)"/>
      <polygon class="card-stripe" points="481,0 495,0 166,403 151,403" fill="var(--stripe-grey)"/>
    </svg>

    <div class="contact-block">
      <h1 class="owner-name">PAUL DUNMORE</h1>
      <p class="owner-role">Owner</p>
      <div class="contact-line contact-email">
        <svg viewBox="0 0 24 24" aria-hidden="true"><rect x="2" y="5" width="20" height="14" fill="#fff"/><path d="M2 5 L12 13 L22 5" fill="none" stroke="var(--brand-blue)" stroke-width="2"/></svg>
        <span>paul@dunmoreroofing-example.com</span>
      </div>
      <div class="contact-line contact-web">
        <svg viewBox="0 0 24 24" aria-hidden="true"><circle cx="12" cy="12" r="10" fill="#fff"/><path d="M2 12h20M12 2c-4 4-4 16 0 20M12 2c4 4 4 16 0 20" fill="none" stroke="var(--brand-blue)" stroke-width="1.6"/></svg>
        <span>www.dunmoreroofing-example.com</span>
      </div>
      <address class="address">4172 Township road 43<br>Ashcombe,ON K9X4T2</address>
    </div>

    <p class="brand-name"><span>DUNMORE</span><span>ROOFING</span></p>
  </div>
</body>
</html>
```